Harwick Moss Fine Art gallery website - Modern british art for sale

We need a website design that is both current and high end. Our products are expensive and this should be reflected in the look of the website. We would like the logo we had designed last year to be clearly seen in the design. We want sleek, simple, and easy to navigate. Nothing too colourful as the colours of the art should always take precedence.

Target Market(s)

The average price of one our products starts at £250 and can go up to £10,000 we are an entry level gallery.

Industry/Entity Type

Art Gallery

Number of Pages Required

5+ page

Font styles to use
Sans Serif

Colors
000000
ffffff
faa54b
abd037
886aae
b868aa

Requirements
Must have
• Attractive front page. Linked to our Twitter feed.
• 4 links from front page - New Releases, about us, Artists, contact us
• Social media links - Facebook, Twitter, YouTube, Instagram.
• Each artist must have their own page, each page must have a biography link to another page.
Nice to have
• Utilise our new logo design. I would like the Twitter feed to link to the front page in a small way so you can see what's being said on Twitter by the company. For future proofing maybe have a locations function on the front page which can be adroit down menu showing where our other galleries are.

```html
<!DOCTYPE html>
<html lang="en">
<head>
<meta charset="utf-8">
<title>Harwick Moss Fine Art</title>
<link rel="stylesheet" href="https://fonts.googleapis.com/css2?family=Cinzel:wght@400;700&family=Lato:wght@400;700&display=swap">
<style>
:root{
  --ink:#1c1c1c;
  --text:#3a3a3a;
  --muted:#6b6b6b;
  --orange:#faa54b;
  --purple:#b868aa;
  --violet:#886aae;
  --green:#abd037;
  --white:#ffffff;
  --rule:#e2e2e2;
  --band:rgba(244,244,244,.95);
  --footer:#1f1f1f;
  --link:#3b94d9;
}
*{margin:0;padding:0;box-sizing:border-box}
html,body{width:1200px;height:2179px;overflow:hidden;background:var(--white)}
body{position:relative;font-family:'Lato',sans-serif;color:var(--text)}
.abs{position:absolute}

/* hero */
.hero-art{left:0;top:0;width:1200px;height:581px;
  background:linear-gradient(180deg,#6fb9c2 0%,#9fcfc4 22%,#e8d98a 45%,#f4d35a 62%,#9fc24a 78%,#f0a23a 92%,#ee7a2a 100%)}
.nav-band{left:0;top:190px;width:1200px;height:167px;background:var(--band)}
.nav-band .row{position:absolute;left:0;width:1200px;height:1px;background:#dcdcdc}
.nav-link{left:285px;font-family:'Cinzel',serif;font-weight:700;font-size:12px;color:var(--ink);letter-spacing:.5px}
.brand{left:250px;top:100px;width:128px;height:71px;background:#262626;border:1px solid #444;display:flex;align-items:center;justify-content:center;text-align:center;font-family:'Lato',sans-serif;font-size:11px;color:#d9d9d9;line-height:1.3;letter-spacing:.5px}
.hero-ring{left:414px;top:29px;width:508px;height:508px;border-radius:50%;background:var(--white);box-shadow:0 0 6px rgba(0,0,0,.15)}
.hero-feature{left:423px;top:38px;width:490px;height:490px;border-radius:50%;overflow:hidden;background:#e4e2d4}
.hero-feature .art{position:absolute;inset:0;background:radial-gradient(circle at 50% 45%,#c85a8a 0%,#6a5ab0 22%,#f07a3a 40%,#e4e2d4 62%)}
.welcome{left:494px;top:452px;width:349px;height:42px;background:var(--orange);color:var(--white);font-family:'Cinzel',serif;font-size:16px;letter-spacing:1px;display:flex;align-items:center;justify-content:center}
.slider-bar{left:537px;top:494px;width:263px;height:32px;background:#d8d8d8;display:flex;align-items:center;justify-content:center;gap:12px}

/* headings */
.section-title{left:0;width:1200px;text-align:center;font-family:'Cinzel',serif;font-size:29px;color:var(--ink);letter-spacing:1px}
.section-title span{color:var(--purple)}
.title-rule{height:1px;background:#cfcfcf}
.title-rule::after{content:"";position:absolute;left:50%;top:-1px;width:28px;height:3px;margin-left:-14px;background:var(--orange)}
.divider{left:160px;width:879px;height:1px;background:var(--rule)}

/* releases */
.release{width:300px;text-align:center}
.release .hang{display:block;margin:0 auto}
.release .disc{width:186px;height:186px;border-radius:50%;margin:-4px auto 0;border:1px solid #999}
.release h3{font-size:15px;font-weight:700;color:var(--ink);margin-top:16px}
.release p{font-size:11.5px;line-height:19px;margin-top:6px;color:var(--text)}
.arrow{top:816px}

/* gallery */
.work{width:180px}
.work .frame{width:180px;height:209px}
.work h4{font-size:14px;font-weight:700;color:var(--ink);margin-top:12px}
.work p{font-size:11.5px;line-height:19px;letter-spacing:1.4px;margin-top:5px;color:var(--muted)}
.feed-widget{left:769px;top:1181px;width:268px;height:310px;border:1px solid #d6d6d6;background:var(--white);padding:8px 10px}
.feed-widget .head{font-size:14px;color:var(--ink)}
.feed-widget .head small{font-size:9px;color:var(--muted)}
.feed-widget .head a{font-size:9px;color:var(--link);text-decoration:none}
.feed-widget .feed{position:absolute;left:10px;top:32px;width:240px;height:238px;border-top:1px solid #e6e6e6}
.feed-widget .who{display:flex;gap:6px;margin-top:6px;font-size:9px}
.feed-widget .who i{width:18px;height:18px;background:#555;display:block}
.feed-widget .who b{color:var(--ink)}
.feed-widget .msg{font-size:8.5px;line-height:12px;margin:2px 0 0 24px;color:var(--text)}
.feed-widget .pic{margin:12px 0 0 6px;width:199px;height:141px;background:linear-gradient(135deg,#cfcfcf,#8e8e8e 60%,#bdbdbd)}
.feed-widget .scroll{position:absolute;right:10px;top:36px;width:10px;height:230px;background:#f0f0f0;border:1px solid #ddd}
.feed-widget .foot{position:absolute;left:16px;right:22px;bottom:14px;display:flex;justify-content:space-between;font-size:7.5px;color:var(--link)}

/* about / artists */
.block-title{font-family:'Cinzel',serif;font-size:29px;color:var(--ink);letter-spacing:1px}
.block-title span{color:var(--purple)}
.block-rule{height:1px;background:#d6d6d6}
.block-rule::after{content:"";position:absolute;left:0;top:-1px;width:28px;height:3px;background:var(--orange)}
.about-copy{left:161px;width:430px;font-size:11.5px;line-height:21px;color:var(--text)}
.btn{left:161px;top:1912px;width:101px;height:30px;background:var(--orange);color:var(--white);font-size:11px;display:flex;align-items:center;justify-content:center;border-radius:2px}
.pager{font-size:11px;color:var(--orange)}
.artist-card{left:628px;top:1685px;width:194px;height:257px;background:linear-gradient(180deg,#b7a88c,#8b6c55 60%,#6d5442)}
.artist-card .info{position:absolute;left:0;bottom:0;width:194px;height:81px;background:rgba(250,165,75,.88);color:var(--white);text-align:center;font-size:10.5px;line-height:17px;padding-top:12px}
.artist-card .social{display:flex;justify-content:center;gap:16px;margin-top:6px}
.artist-card .social i{display:block;width:8px;height:8px;border-radius:50%;background:var(--white)}
.artist-photo{left:867px;top:1650px;width:170px;height:237px;background:linear-gradient(160deg,#6a4a3a,#8ab0c8 55%,#d6dde2);border:1px solid #ccc}

/* footer */
.footer{left:0;top:1987px;width:1200px;height:154px;background:var(--footer);color:var(--white)}
.contact{display:flex;gap:11px;align-items:flex-start;font-size:11.5px;line-height:15px;top:38px}
.contact .ico{width:30px;height:30px;border-radius:50%;background:var(--white);flex:none;display:flex;align-items:center;justify-content:center}
.foot-nav{top:107px;left:0;width:1200px;display:flex;justify-content:center;gap:22px;font-size:10.5px}
.foot-nav em{font-style:normal;color:#777}
.copyright{left:0;top:2141px;width:1200px;height:38px;background:var(--orange);color:var(--white);font-size:11px;display:flex;align-items:center;justify-content:center}
</style>
</head>
<body>

<header>
  <div class="abs hero-art" role="img" aria-label="Painted landscape of sky, clouds, birds and a golden meadow with a figure holding an umbrella"></div>
  <nav class="abs nav-band" aria-label="Main">
    <div class="row" style="top:41px"></div>
    <div class="row" style="top:83px"></div>
    <div class="row" style="top:125px"></div>
  </nav>
  <a class="abs nav-link" style="top:204px">New Releases</a>
  <a class="abs nav-link" style="top:246px">About us</a>
  <a class="abs nav-link" style="top:288px">Artists</a>
  <a class="abs nav-link" style="top:329px">Contact us</a>
  <div class="abs brand">Harwick Moss<br>Fine Art</div>

  <div class="abs hero-ring"></div>
  <div class="abs hero-feature"><div class="art" role="img" aria-label="Colourful abstract portrait painting in purple, orange and blue on a pale ground"></div></div>
  <div class="abs welcome">Welcome to Harwickmossfineart</div>
  <div class="abs slider-bar">
    <svg width="8" height="12" viewBox="0 0 8 12"><path d="M6 1 1 6l5 5" fill="none" stroke="#333" stroke-width="1.6"/></svg>
    <svg width="8" height="12" viewBox="0 0 8 12"><path d="M2 1l5 5-5 5" fill="none" stroke="#333" stroke-width="1.6"/></svg>
  </div>
</header>

<section>
  <h2 class="abs section-title" style="top:616px">New <span>Releases</span></h2>
  <div class="abs title-rule" style="left:462px;top:670px;width:276px"></div>

  <svg class="abs arrow" style="left:100px" width="16" height="36" viewBox="0 0 16 36"><path d="M14 2 2 18l12 16" fill="none" stroke="#999" stroke-width="1.5"/></svg>
  <svg class="abs arrow" style="left:1084px" width="16" height="36" viewBox="0 0 16 36"><path d="M2 2l12 16L2 34" fill="none" stroke="#999" stroke-width="1.5"/></svg>

  <div class="abs release" style="left:145px;top:692px">
    <svg class="hang" width="140" height="48" viewBox="0 0 140 48"><path d="M70 10 18 48M70 10l52 38" stroke="#888" fill="none"/><circle cx="70" cy="8" r="6" fill="var(--orange)"/></svg>
    <div class="disc" role="img" aria-label="Grey etching of seated figures" style="background:radial-gradient(circle,#dcdcdc,#9a9a9a)"></div>
    <h3>Seated Figures</h3>
    <p>Lorem ipsum dolor sit amet, consectetuer<br>adipiscing elit, sed diam nonummy nibh euismod<br>tincidunt ut laoreet dolore magna.</p>
  </div>
  <div class="abs release" style="left:447px;top:692px">
    <svg class="hang" width="140" height="48" viewBox="0 0 140 48"><path d="M70 10 18 48M70 10l52 38" stroke="#888" fill="none"/><circle cx="70" cy="8" r="6" fill="var(--orange)"/></svg>
    <div class="disc" role="img" aria-label="Teal glass sphere study on grey" style="background:radial-gradient(circle at 50% 40%,#5f9a9c,#c4c4c4 55%,#a9a9a9)"></div>
    <h3>Tideline</h3>
    <p>Lorem ipsum dolor sit amet, consectetuer<br>adipiscing elit, sed diam nonummy nibh euismod<br>tincidunt ut laoreet dolore magna.</p>
  </div>
  <div class="abs release" style="left:749px;top:692px">
    <svg class="hang" width="140" height="48" viewBox="0 0 140 48"><path d="M70 10 18 48M70 10l52 38" stroke="#888" fill="none"/><circle cx="70" cy="8" r="6" fill="var(--orange)"/></svg>
    <div class="disc" role="img" aria-label="Ink drawing of a church spire over a city" style="background:linear-gradient(90deg,#cfcfcf,#3a3a3a 50%,#b65a3a 80%,#cfcfcf)"></div>
    <h3>Harbour Spire</h3>
    <p>Lorem ipsum dolor sit amet, consectetuer<br>adipiscing elit, sed diam nonummy nibh euismod<br>tincidunt ut laoreet dolore magna.</p>
  </div>
</section>

<div class="abs divider" style="top:1065px"></div>

<section>
  <h2 class="abs section-title" style="top:1102px">Art <span>Gallery</span></h2>
  <div class="abs title-rule" style="left:462px;top:1155px;width:276px"></div>

  <div class="abs work" style="left:161px;top:1181px">
    <div class="frame" role="img" aria-label="Black and white line etching" style="background:linear-gradient(135deg,#f2f2f2,#9a9a9a 50%,#eaeaea)"></div>
    <h4>Loxley Etching</h4>
    <p>Lorem ipsum dolor sit amet adipiscing elit, sed diam nonummy</p>
  </div>
  <div class="abs work" style="left:363px;top:1181px">
    <div class="frame" role="img" aria-label="Framed watercolour print on a white shelf" style="background:radial-gradient(circle,#7fb4e0 0%,#eef0f2 30%,#e6e6e6)"></div>
    <h4>Loxley Etching</h4>
    <p>Lorem ipsum dolor sit amet adipiscing elit, sed diam nonummy</p>
  </div>
  <div class="abs work" style="left:565px;top:1181px">
    <div class="frame" role="img" aria-label="Colourful splash painting in red, yellow and teal" style="background:radial-gradient(circle at 45% 50%,#2aa89a,#e8402a 35%,#f3c23a 60%,#f3efc8)"></div>
    <h4>Loxley Etching</h4>
    <p>Lorem ipsum dolor sit amet adipiscing elit, sed diam nonummy</p>
  </div>

  <aside class="abs feed-widget">
    <div class="head">Posts <small>by</small> <a>@harwickmossart</a></div>
    <div class="feed">
      <div class="who"><i></i><span><b>Harwickmossfineart</b> <span style="color:#888">@Harwickmoss</span></span></div>
      <div class="msg">Lorem ipsum dolor sit amet, consectetuer ,<br>sed diam nonummy nibh euismod</div>
      <div class="pic" role="img" aria-label="Shared etching of abstract forms"></div>
    </div>
    <div class="scroll"></div>
    <div class="foot"><span>Embed</span><span>View full feed</span></div>
  </aside>
</section>

<div class="abs divider" style="top:1536px"></div>

<section>
  <h2 class="abs block-title" style="left:161px;top:1575px">About <span>us</span></h2>
  <div class="abs block-rule" style="left:161px;top:1627px;width:427px"></div>
  <p class="abs about-copy" style="top:1650px">Lorem ipsum dolor sit amet, consectetuer adipiscing elit, sed diam nonummy nibh euismod tincidunt ut laoreet dolore magna aliquam erat volutpat. Ut wisi enim ad minim veniam, quis nostrud exerci tation ullamcorper suscipit lobortis nisl ut aliquip ex ea commodo consequat. Duis autem vel eum iriure dolor in hendrerit in vulputate velit esse molestie consequat, vel illum dolore eu feugiat nulla facilisis at vero eros et accumsan et iusto odio dignissim qui blandit</p>
  <p class="abs about-copy" style="top:1790px">Lorem ipsum dolor sit amet, consectetuer adipiscing elit, sed diam nonummy nibh euismod tincidunt ut laoreet dolore magna aliquam erat volutpat. Ut wisi enim ad minim veniam, quis nostrud exerci tation ullamcorper suscipit lobortis nisl ut aliquip ex ea commodo consequat. Duis autem vel eum iriure dolor in hendrerit in vulputate velit esse molestie consequat, vel illum dolore</p>
  <a class="abs btn">Rad More</a>

  <h2 class="abs block-title" style="left:629px;top:1575px">Our <span>Artists</span></h2>
  <div class="abs block-rule" style="left:629px;top:1627px;width:424px"></div>
  <span class="abs pager" style="left:628px;top:1651px">‹&nbsp; Previous</span>
  <div class="abs artist-card" role="img" aria-label="Portrait photograph of a gallery co-founder">
    <div class="info">Mara Ellwood<br>Co-Founder
      <div class="social"><i></i><i></i><i></i><i></i></div>
    </div>
  </div>
  <div class="abs artist-photo" role="img" aria-label="Photograph of an artist standing beside a painting"></div>
  <span class="abs pager" style="left:1001px;top:1908px">Next &nbsp;›</span>
</section>

<footer class="abs footer">
  <div class="abs contact" style="left:260px">
    <span class="ico"><svg width="14" height="14" viewBox="0 0 24 24"><path d="M6.6 10.8a15 15 0 0 0 6.6 6.6l2.2-2.2a1 1 0 0 1 1-.25 11.4 11.4 0 0 0 3.6.57 1 1 0 0 1 1 1V20a1 1 0 0 1-1 1A17 17 0 0 1 3 4a1 1 0 0 1 1-1h3.5a1 1 0 0 1 1 1c0 1.25.2 2.45.57 3.57a1 1 0 0 1-.25 1z" fill="#1f1f1f"/></svg></span>
    <span>Call<br>0161 555 0142</span>
  </div>
  <div class="abs contact" style="left:479px">
    <span class="ico"><svg width="14" height="12" viewBox="0 0 24 20"><path d="M2 2h20v16H2z" fill="#1f1f1f"/><path d="M2 3l10 8 10-8" fill="none" stroke="#fff" stroke-width="2"/></svg></span>
    <span>Email<br>hello@harwickmossart.com</span>
  </div>
  <div class="abs contact" style="left:755px">
    <span class="ico"><svg width="12" height="16" viewBox="0 0 24 32"><path d="M12 0a11 11 0 0 0-11 11c0 8 11 21 11 21s11-13 11-21A11 11 0 0 0 12 0z" fill="#1f1f1f"/><circle cx="12" cy="11" r="4" fill="#fff"/></svg></span>
    <span>Level 5 Almond Tower<br>12 Kestrel Road Bramley<br>QLD 4012</span>
  </div>
  <nav class="abs foot-nav" aria-label="Footer">
    <a>New Releases</a><em>|</em><a>About Us</a><em>|</em><a>Artists</a><em>|</em><a>Contact Us</a>
  </nav>
</footer>
<div class="abs copyright">Copyright © 2016 Harwickmossfineart.All Rights Reserved</div>

</body>
</html>
```